Bramblewick Forage Business Cards

I need a business card with my logo, number, Facebook account, and some information about what I am selling. Green card with logo on the front. 555-214-8392 phone number, @bramblewickforage Facebook, •Orchardgrass Hay •Alfalfa Hay •Mixed Grass Hay , and “Premium Quality Hay” all written on the back.

Target Market(s)

Hay

Contact Information for Business Card

Phone number, Facebook, different types of hay.

Colors
00AB8E
00BBA5
67D7C9
C6EFE9
E9F9F6

```html
<!DOCTYPE html>
<html lang="en">
<head>
<meta charset="utf-8">
<title>Bramblewick Forage Business Cards</title>
<link href="https://fonts.googleapis.com/css2?family=Kaushan+Script&family=Arimo:wght@400;700&display=swap" rel="stylesheet">
<style>
  :root {
    --stage: #262626;
    --stage-edge: #151515;
    --brand-green: #00a651;
    --card-white: #ffffff;
    --ink: #1a1a1a;
    --rule-grey: #bdbdbd;
    --faint: #f0f0f0;
  }
  * { box-sizing: border-box; margin: 0; padding: 0; }
  html, body { width: 1200px; height: 1015px; overflow: hidden; }
  body {
    background: radial-gradient(ellipse at center, var(--stage) 0%, var(--stage-edge) 100%);
    font-family: "Arimo", Arial, sans-serif;
    position: relative;
  }
  .card {
    position: absolute;
    left: 290px;
    width: 620px;
    height: 354px;
    overflow: hidden;
  }
  /* Front */
  .card-front { top: 70px; background: var(--brand-green); }
  .front-mark {
    position: absolute; left: 64px; top: 132px;
  }
  .mark-dot {
    display: block;
    width: 100px; height: 100px; border-radius: 50%;
    background: var(--ink);
  }
  .front-info {
    position: absolute; left: 196px; top: 118px;
    color: var(--card-white);
    white-space: nowrap;
  }
  .front-name {
    font-family: "Kaushan Script", cursive;
    font-size: 40px; line-height: 1.15;
  }
  .front-phone {
    font-family: "Arimo", Arial, sans-serif;
    font-weight: 700; font-size: 44px; letter-spacing: 1px;
    margin-top: 4px;
  }
  /* Back */
  .card-back { top: 590px; background: var(--card-white); }
  .back-accent {
    position: absolute; left: -60px; top: 180px;
    width: 260px; height: 120px; border-radius: 50%;
    background: var(--faint);
  }
  .back-header {
    position: absolute; left: 50px; top: 36px; right: 30px;
    display: flex; align-items: center;
    white-space: nowrap;
  }
  .back-mark {
    display: flex; align-items: center; width: 130px; justify-content: center;
  }
  .back-mark .mark-dot { width: 84px; height: 84px; background: var(--brand-green); }
  .header-divider {
    width: 1px; height: 92px; background: var(--rule-grey); margin: 0 20px 0 18px;
  }
  .back-name {
    font-family: "Kaushan Script", cursive;
    font-size: 31px; color: var(--ink); line-height: 1.2;
  }
  .rule {
    position: absolute; height: 1px; background: var(--brand-green);
  }
  .rule-top { left: 240px; right: 30px; top: 148px; }
  .rule-bottom { left: 40px; right: 30px; top: 250px; }
  .contact-row {
    position: absolute; left: 40px; right: 30px; top: 176px;
    display: flex; gap: 48px; align-items: center;
    font-size: 21px; color: var(--ink); letter-spacing: 0.5px;
    white-space: nowrap;
  }
  .contact-item { display: flex; align-items: center; gap: 10px; }
  .contact-icon {
    width: 40px; height: 40px; border-radius: 50%;
    background: var(--brand-green);
    display: flex; align-items: center; justify-content: center;
    flex: none;
  }
  .product-list {
    position: absolute; left: 40px; top: 268px;
    display: grid; grid-template-columns: 250px 300px; row-gap: 6px;
    list-style: none; font-size: 23px; color: var(--ink); letter-spacing: 0.5px;
    white-space: nowrap;
  }
  .product-list li { display: flex; align-items: center; gap: 10px; }
  .product-list li::before {
    content: ""; width: 13px; height: 13px; border-radius: 50%;
    background: var(--brand-green);
  }
</style>
</head>
<body>
  <section class="card card-front" aria-label="Card front">
    <div class="front-mark">
      <span class="mark-dot"></span>
    </div>
    <div class="front-info">
      <div class="front-name">Bramblewick Forage</div>
      <div class="front-phone">555-214-8392</div>
    </div>
  </section>

  <section class="card card-back" aria-label="Card back">
    <div class="back-accent" aria-hidden="true"></div>
    <div class="back-header">
      <div class="back-mark"><span class="mark-dot"></span></div>
      <div class="header-divider"></div>
      <div class="back-name">Bramblewick Forage</div>
    </div>
    <div class="rule rule-top"></div>
    <div class="contact-row">
      <div class="contact-item">
        <span class="contact-icon">
          <svg width="22" height="22" viewBox="0 0 24 24" aria-hidden="true">
            <path fill="#fff" d="M6.6 10.8a15.1 15.1 0 0 0 6.6 6.6l2.2-2.2a1 1 0 0 1 1-.25 11.4 11.4 0 0 0 3.6.57 1 1 0 0 1 1 1V20a1 1 0 0 1-1 1A17 17 0 0 1 3 4a1 1 0 0 1 1-1h3.5a1 1 0 0 1 1 1c0 1.25.2 2.45.57 3.57a1 1 0 0 1-.25 1z"/>
          </svg>
        </span>
        <span>555-214-8392</span>
      </div>
      <div class="contact-item">
        <span class="contact-icon"></span>
        <span>@bramblewickforage</span>
      </div>
    </div>
    <div class="rule rule-bottom"></div>
    <ul class="product-list">
      <li>Orchardgrass Hay</li>
      <li>Alfalfa Hay</li>
      <li>Mixed Grass Hay</li>
      <li>Premium Quality Hay</li>
    </ul>
  </section>
</body>
</html>
```